Social media agency for startUps! Need captivating web banner(s) needed

We need a few banners if Possible for a lead generation - branding campaign we are about to launch on Workvine & Chatterloop. We are Social media Agency created to help Startup and small medium business build there digital footprint. We also offer a brand analysing service to help brands understand there real time impact along with consulting, coaching and managed services. We are very open to the design concept. We are looking for creativity and professionalism. Something that will captivate and peek interest in learning more about how a company can work with us. We are need banners for Chatterloop and Workvine. If you require the formats please ask and we will send them. 2 for each platform would be nice, but depending on cost we would be happy with i for each network.

Designs should have our tag line : Accelerated Marketing. Refreshing Results. it should alsl speak to the fact that we are the Social Media Agency for Startups in Canada.

Target Market(s)

Small Medium Business and Start up companies

Industry/Entity Type

Media

Requirements
Must have
• company name - TrailMOSS Social
• out tag line - Accelerated Marketing. Refreshing Results
• our Logo -
• ad size -
• 160x600 Workvine
• 30x250 Workvine
• 1,200 x 628 pixels Chatterloop
• Recommended image size: 600 x 600 pixels
Nice to have
• This is the hard part - I would like to see something like a collage of all the social networks and how our brand connects them to the business in question. The other aspect could be something related to when you leveled up in a video game.
• i know this is somewhat vague, but i am open to any question you might have relating to this project.

```html
<!DOCTYPE html>
<html lang="en">
<head>
<meta charset="utf-8">
<title>TrailMOSS Social – Accelerated Marketing</title>
<link rel="stylesheet" href="https://fonts.googleapis.com/css2?family=Oswald:wght@400;500&family=Roboto:wght@400&display=swap">
<style>
  :root {
    --navy: #27252f;
    --orange: #f7941d;
    --orange-deep: #f26522;
    --edge-light: #e9e7ec;
    --bullet-grey: #a9a8b2;
    --white: #ffffff;
    --photo-light: #eef0f2;
    --photo-mid: #c9ccd1;
  }
  html, body {
    margin: 0;
    padding: 0;
    width: 1200px;
    height: 1200px;
    overflow: hidden;
    background: var(--white);
  }
  .banner {
    position: relative;
    width: 1200px;
    height: 1200px;
    overflow: hidden;
  }
  .banner__backdrop {
    position: absolute;
    inset: 0;
  }
  .brand {
    position: absolute;
    left: 48px;
    top: 96px;
    width: 460px;
    text-align: center;
  }
  .brand__mark {
    width: 110px;
    height: 110px;
    margin: 0 auto 50px;
    background: var(--orange);
  }
  .brand__name {
    margin: 0;
    font-family: "Oswald", sans-serif;
    font-weight: 500;
    font-size: 36px;
    line-height: 1;
    letter-spacing: 6px;
    color: var(--white);
    text-transform: uppercase;
  }
  .brand__tagline {
    margin: 10px 0 0;
    font-family: "Roboto", sans-serif;
    font-size: 24px;
    color: var(--white);
  }
  .services {
    position: absolute;
    left: 58px;
    top: 406px;
    margin: 0;
    padding: 0;
    list-style: none;
  }
  .services__item {
    position: relative;
    padding-left: 46px;
    font-family: "Oswald", sans-serif;
    font-weight: 400;
    font-size: 45px;
    line-height: 88px;
    color: var(--bullet-grey);
    text-transform: uppercase;
    white-space: nowrap;
  }
  .services__item::before {
    content: "";
    position: absolute;
    left: 4px;
    top: 40px;
    width: 9px;
    height: 9px;
    border-radius: 50%;
    background: var(--bullet-grey);
  }
  .slogan {
    position: absolute;
    left: 48px;
    top: 920px;
    margin: 0;
    font-family: "Oswald", sans-serif;
    font-weight: 500;
    font-size: 47px;
    line-height: 82px;
    text-transform: uppercase;
  }
  .slogan__accent { display: block; color: var(--orange); }
  .slogan__plain { display: block; color: var(--white); }
</style>
</head>
<body>
  <main class="banner">
    <svg class="banner__backdrop" width="1200" height="1200" viewBox="0 0 1200 1200">
      <defs>
        <linearGradient id="photoTone" x1="0" y1="0" x2="1" y2="1">
          <stop offset="0" stop-color="#eef0f2"/>
          <stop offset="0.55" stop-color="#c9ccd1"/>
          <stop offset="1" stop-color="#eef0f2"/>
        </linearGradient>
        <linearGradient id="edgeGlow" x1="0" y1="0" x2="0" y2="1">
          <stop offset="0" stop-color="#f7941d"/>
          <stop offset="0.5" stop-color="#f26522"/>
          <stop offset="1" stop-color="#f7941d"/>
        </linearGradient>
      </defs>
      <rect class="photo-area" x="0" y="0" width="1200" height="1200" fill="url(#photoTone)" role="img" aria-label="Photo of a hand holding a smartphone with colourful social media app icons floating above the screen"/>
      <polygon class="chevron-edge-light" points="0,0 548,0 768,600 548,1200 0,1200" fill="var(--edge-light)" opacity="0.85"/>
      <polygon class="chevron-edge-orange" points="0,0 538,0 758,600 538,1200 0,1200" fill="url(#edgeGlow)"/>
      <polygon class="chevron-panel" points="0,0 526,0 746,600 526,1200 0,1200" fill="var(--navy)"/>
    </svg>

    <header class="brand">
      <div class="brand__mark"></div>
      <h1 class="brand__name">TrailMOSS Social</h1>
      <p class="brand__tagline">Accelerated Marketing, Refreshing results</p>
    </header>

    <ul class="services">
      <li class="services__item">Brand Analysing Service</li>
      <li class="services__item">Consulting</li>
      <li class="services__item">Coaching &amp; Managed Services</li>
      <li class="services__item">Online Marketing</li>
      <li class="services__item">Social Media</li>
    </ul>

    <p class="slogan">
      <span class="slogan__accent">Accelerated Marketing.</span>
      <span class="slogan__plain">Refreshing Results</span>
    </p>
  </main>
</body>
</html>
```